KDWB Business Card

Looking for a business card design to incorporate our branding. We want to only use the colors listing in the Branding Package (attached).
Updates

Target Market(s)

People who need their phone or device fixed.

Industry/Entity Type

Electronics

Contact Information for Business Card

Please use:

Brightwick Gadget Clinic LLC
4810 E Harlow Ridge Rd
Suite 417
San Antonio, TX 78163

Marcus Delgrove, Store Manager

(210) 555-0147

Requirements
Must have
• Must include the colors that are contained within the Branding Package PDF file.

```html
<!DOCTYPE html>
<html lang="en">
<head>
<meta charset="utf-8">
<title>Brightwick Gadget Clinic – Business Card</title>
<link rel="stylesheet" href="https://fonts.googleapis.com/css2?family=Questrial&display=swap">
<style>
  :root {
    --backdrop: #e6e6e4;
    --card: #ffffff;
    --slate: #54565a;
    --orange: #f0521d;
    --ink-light: #e4e4e4;
    --shadow: rgba(0, 0, 0, 0.18);
  }
  * { box-sizing: border-box; margin: 0; padding: 0; }
  html, body { width: 1200px; height: 873px; overflow: hidden; }
  body {
    background: var(--backdrop);
    font-family: "Questrial", "Century Gothic", sans-serif;
    position: relative;
  }
  .card {
    position: absolute;
    top: 288px;
    width: 520px;
    height: 297px;
    background: var(--card);
    box-shadow: 0 6px 18px var(--shadow);
    overflow: hidden;
  }
  .card--front { left: 50px; }
  .card--back { left: 630px; }

  .card__art { position: absolute; inset: 0; width: 100%; height: 100%; }

  .brand {
    position: absolute;
    display: flex;
    align-items: center;
    gap: 10px;
    color: var(--orange);
    white-space: nowrap;
  }
  .brand__mark {
    width: 26px;
    height: 26px;
    background: var(--orange);
    flex: none;
  }
  .brand__name { font-size: 22px; letter-spacing: 0.2px; }
  .card--front .brand { left: 170px; top: 40px; }
  .card--back .brand { left: 50%; top: 50%; transform: translate(-50%, -50%); }

  .person {
    position: absolute;
    right: 352px;
    top: 134px;
    text-align: right;
    color: var(--ink-light);
  }
  .person__name { font-size: 20px; letter-spacing: 0.3px; white-space: nowrap; }
  .person__title { font-size: 10px; margin-top: 4px; }

  .divider {
    position: absolute;
    left: 182px;
    top: 130px;
    width: 1px;
    height: 138px;
    background: var(--ink-light);
  }

  .contact {
    position: absolute;
    left: 196px;
    top: 212px;
    color: var(--ink-light);
    font-size: 10.5px;
    line-height: 1.45;
    white-space: nowrap;
  }
  .contact__row { display: flex; align-items: flex-start; gap: 7px; margin-bottom: 5px; }
  .contact__icon {
    width: 11px;
    height: 11px;
    background: var(--orange);
    flex: none;
    margin-top: 1px;
  }
  .contact__icon svg { display: block; width: 11px; height: 11px; }
</style>
</head>
<body>

  <section class="card card--front" aria-label="Business card front">
    <svg class="card__art" viewBox="0 0 520 297" aria-hidden="true">
      <path class="card__band" fill="var(--slate)"
            d="M0,110 C110,100 180,112 235,150 C300,196 390,220 520,220 L520,297 L0,297 Z"/>
      <path class="card__swoosh" fill="var(--orange)"
            d="M244,140 C308,184 398,204 520,202 L520,212 C394,213 304,192 238,146 Z"/>
    </svg>

    <div class="brand">
      <span class="brand__mark"></span>
      <span class="brand__name">Brightwick Gadget Clinic</span>
    </div>

    <div class="person">
      <p class="person__name">Marcus Delgrove</p>
      <p class="person__title">Store Manager</p>
    </div>

    <span class="divider"></span>

    <div class="contact">
      <div class="contact__row">
        <span class="contact__icon">
          <svg viewBox="0 0 11 11"><path fill="#fff" d="M3.2 2.2 L4.4 3.6 L3.8 4.4 C4.3 5.4 5.1 6.2 6.1 6.7 L6.9 6.1 L8.3 7.3 L7.6 8.6 C5 8.3 2.7 6 2.4 3.4 Z"/></svg>
        </span>
        <span>(210) 555-0147</span>
      </div>
      <div class="contact__row">
        <span class="contact__icon">
          <svg viewBox="0 0 11 11"><path fill="#fff" d="M5.5 2 C4 2 3 3.1 3 4.5 C3 6.3 5.5 9 5.5 9 C5.5 9 8 6.3 8 4.5 C8 3.1 7 2 5.5 2 Z M5.5 5.4 A0.9 0.9 0 1 1 5.5 3.6 A0.9 0.9 0 1 1 5.5 5.4 Z"/></svg>
        </span>
        <span>4810 E Harlow Ridge Rd<br>Suite 417, San Antonio, TX 78163</span>
      </div>
    </div>
  </section>

  <section class="card card--back" aria-label="Business card back">
    <div class="brand">
      <span class="brand__mark"></span>
      <span class="brand__name">Brightwick Gadget Clinic</span>
    </div>
  </section>

</body>
</html>
```